Business card for law firm

Need business card for new law firm. Think confident, authoritative, conservative, but not stuffy or old-fashioned.

Contact Information for Business Card

Content for card - logo (uploaded), plus the following:

Paul Whitcombe (larger font)
Managing Partner (larger font, but not as large as name)
Level 9, 7 Ferris Lane
Sydney NSW 2000
Main Tel 02 9364 2710
Direct Tel 02 8472 3159
Email paul@qvlegal.com.au
www.qvlegal.com.au

Letterhead design should include logo plus:
Level 9, 7 Ferris Lane
Sydney NSW 2000
Tel 02 8472 3159
www.qvlegal.com.au

```html
<!DOCTYPE html>
<html lang="en">
<head>
<meta charset="utf-8">
<title>Quayvale Lawyers – Business Card</title>
<link href="https://fonts.googleapis.com/css2?family=EB+Garamond:wght@500&family=Open+Sans:wght@400;600&display=swap" rel="stylesheet">
<style>
  :root {
    --navy: #0d1f5c;
    --navy-deep: #0a1a4f;
    --navy-soft: #1a2d6e;
    --ink: #111111;
    --text: #2b2b2b;
    --muted: #555a66;
    --paper: #ffffff;
    --stage: #e6e7ea;
  }
  * { margin: 0; padding: 0; box-sizing: border-box; }
  html, body { width: 1200px; height: 782px; overflow: hidden; background: var(--stage); }
  .stage {
    position: relative; width: 1200px; height: 782px;
    display: flex; align-items: center; justify-content: center; gap: 44px;
  }
  .card {
    position: relative; width: 520px; height: 298px; overflow: hidden;
    box-shadow: 0 6px 18px rgba(0,0,0,0.18);
  }
  .card-front { background: var(--paper); }
  .holder { position: absolute; left: 30px; top: 26px; }
  .holder-name {
    font-family: "EB Garamond", serif; font-weight: 500;
    font-size: 21px; letter-spacing: 0.5px; color: var(--navy); text-transform: uppercase;
    line-height: 1;
  }
  .holder-title {
    font-family: "Open Sans", sans-serif; font-size: 13px; color: var(--muted); margin-top: 3px;
  }
  .contacts {
    position: absolute; left: 30px; top: 152px; list-style: none;
    font-family: "Open Sans", sans-serif; font-size: 12px; color: var(--text); line-height: 17px;
  }
  .contacts li { display: flex; align-items: center; gap: 6px; }
  .contacts svg { width: 10px; height: 10px; fill: var(--navy); flex: none; }
  .firm {
    position: absolute; left: 250px; top: 128px; width: 250px;
    display: flex; align-items: center; justify-content: center; gap: 10px;
  }
  .firm-square { width: 22px; height: 22px; background: var(--navy); flex: none; }
  .firm-name {
    font-family: "Open Sans", sans-serif; font-weight: 600; color: var(--ink);
    font-size: 20px; line-height: 1; white-space: nowrap;
  }
  .address {
    position: absolute; right: 28px; bottom: 36px; text-align: right;
    font-family: "Open Sans", sans-serif; font-size: 13px; color: var(--text); line-height: 17px;
  }
  .edge-band { position: absolute; left: 0; bottom: 0; width: 520px; height: 24px; }
  .card-back { background: var(--navy-deep); }
  .back-pattern {
    position: absolute; inset: 0;
    background: linear-gradient(135deg, var(--navy-soft) 0%, var(--navy-deep) 55%, var(--navy-soft) 100%);
  }
  .back-mark {
    position: absolute; right: 120px; bottom: 62px;
    display: flex; align-items: center; gap: 8px;
  }
  .back-square { width: 14px; height: 14px; background: var(--paper); }
  .back-name {
    font-family: "Open Sans", sans-serif; font-weight: 600; font-size: 14px; color: var(--paper);
    white-space: nowrap;
  }
</style>
</head>
<body>
<main class="stage">
  <section class="card card-front">
    <div class="holder">
      <p class="holder-name">Paul Whitcombe</p>
      <p class="holder-title">Managing Partner</p>
    </div>

    <ul class="contacts">
      <li><svg viewBox="0 0 10 10"><path d="M2 0h2l1 2.5-1.3 1a5 5 0 0 0 2.8 2.8l1-1.3L10 6v2a2 2 0 0 1-2 2A8 8 0 0 1 0 2a2 2 0 0 1 2-2z"/></svg>02 9364 2710</li>
      <li><svg viewBox="0 0 10 10"><path d="M2 0h2l1 2.5-1.3 1a5 5 0 0 0 2.8 2.8l1-1.3L10 6v2a2 2 0 0 1-2 2A8 8 0 0 1 0 2a2 2 0 0 1 2-2z"/></svg>02 8472 3159 (DIRECT)</li>
      <li><svg viewBox="0 0 10 10"><path d="M0 2h10v6H0z M0 2l5 3.5L10 2" stroke="#fff" stroke-width="0.8"/></svg>paul@qvlegal.com.au</li>
      <li><svg viewBox="0 0 10 10"><circle cx="5" cy="5" r="5"/><path d="M0 5h10M5 0c-2.5 3-2.5 7 0 10M5 0c2.5 3 2.5 7 0 10" stroke="#fff" stroke-width="0.7" fill="none"/></svg>www.qvlegal.com.au</li>
    </ul>

    <div class="firm">
      <div class="firm-square"></div>
      <p class="firm-name">Quayvale Lawyers</p>
    </div>

    <p class="address">Level 9, 7 Ferris Lane<br>Sydney NSW 2000</p>

    <svg class="edge-band" viewBox="0 0 520 24" preserveAspectRatio="none">
      <polygon points="0,8 236,8 226,24 0,24" fill="var(--navy)"/>
      <polygon points="246,0 520,0 520,24 236,24" fill="var(--ink)"/>
    </svg>
  </section>

  <section class="card card-back">
    <div class="back-pattern" role="img" aria-label="Navy background with a faint repeating brand pattern"></div>
    <div class="back-mark">
      <div class="back-square"></div>
      <p class="back-name">Quayvale Lawyers</p>
    </div>
  </section>
</main>
</body>
</html>
```